Fresh, modern, fun business card for pediatric dental practice

Need a business card for fresh, modern, fun pediatric dental practice

Clean look that matches our website's font and colors

We prefer the look of curved corners on business cards

Target Market(s)

parents (mothers) of young children, professionals, mid-high class

Industry/Entity Type

Dental

Contact Information for Business Card

Maplebrook Pediatric Dentistry
482 Quarry Lane
Suite 517
Fernhill, PA 19990
555.555.0193
www.maplebrookkidsdental.example

Mei-Ran Tsai, DMD
Corinne Walbeck, DMD
(we are working on our email address, but we would like that on the card as well)

Font styles to use
Sans Serif

Requirements
Must have
• All info; we would also like to make cards for individual staff members
• colors from our website and color palatte, attatched
• use same font and design as website for branding
Nice to have
• clean, simple card that has a pop of color
• we would like to see a few designs with our tag line "where smiles get brighter"
• we are not sure if we want to have it on there or not
• we would like to see a few designs incorporating the ribbon graphic on our website where the word WELCOME is

```html
<!DOCTYPE html>
<html lang="en">
<head>
<meta charset="utf-8">
<title>Maplebrook Pediatric Dentistry – Business Card</title>
<link rel="stylesheet" href="https://fonts.googleapis.com/css2?family=Open+Sans:wght@400;600&family=Roboto:wght@400&family=Signika:wght@600&display=swap">
<style>
  :root {
    --plum: #4b2d4b;
    --gold: #e3a10e;
    --magenta: #b2287c;
    --card-white: #f3f3f3;
    --ink: #3a3a3a;
    --backdrop: #bdbdbd;
    --soft-white: #e9e4ea;
  }
  * { margin: 0; padding: 0; box-sizing: border-box; }
  html, body { width: 1200px; height: 576px; overflow: hidden; }
  body { background: var(--backdrop); position: relative; font-family: "Roboto", sans-serif; }

  .card {
    position: absolute;
    top: 138px;
    width: 482px;
    height: 292px;
    border-radius: 14px;
    overflow: hidden;
    box-shadow: 0 3px 6px rgba(0,0,0,0.25);
  }
  .card-front { left: 82px; background: var(--plum); }
  .card-back { left: 602px; background: var(--card-white); }

  .brand-name { font-family: "Open Sans", sans-serif; font-weight: 600; color: var(--gold); }
  .brand-sub { font-family: "Open Sans", sans-serif; font-weight: 400; }
  .brand-mark { display: block; border-radius: 50%; background: var(--gold); }

  /* front */
  .front-brand {
    position: absolute; left: 0; right: 0; top: 60px;
    display: flex; flex-direction: column; align-items: center;
  }
  .front-brand .brand-mark { width: 28px; height: 28px; margin-bottom: 46px; }
  .front-brand .brand-name { font-size: 44px; line-height: 1; letter-spacing: 1px; }
  .front-brand .brand-sub { font-size: 22px; line-height: 1.4; letter-spacing: 1.5px; color: var(--soft-white); }

  .front-url {
    position: absolute; left: 0; right: 0; top: 264px;
    display: flex; justify-content: center; align-items: center; gap: 22px;
    color: var(--soft-white); font-size: 13px; letter-spacing: 0.5px;
  }
  .front-url .url-accent { color: var(--gold); }
  .url-rule { width: 58px; height: 2px; background: linear-gradient(90deg, transparent, var(--magenta) 30%, var(--magenta) 70%, transparent); }

  /* back */
  .back-wave { position: absolute; inset: 0; }
  .back-brand { position: absolute; left: 28px; top: 50px; }
  .back-brand .brand-mark { width: 24px; height: 24px; margin: 0 0 44px 134px; }
  .back-brand .brand-name { font-size: 35px; line-height: 1; letter-spacing: 1px; }
  .back-brand .brand-sub { font-size: 19px; line-height: 1.4; letter-spacing: 1.3px; color: var(--magenta); }

  .doctor-name {
    position: absolute; right: 30px; top: 42px;
    font-family: "Signika", sans-serif; font-weight: 600; font-size: 17px; color: var(--plum);
  }
  .address {
    position: absolute; right: 30px; top: 82px; text-align: right; font-style: normal;
    font-size: 12.5px; line-height: 16px; color: var(--ink);
  }
  .contact-list {
    position: absolute; right: 26px; top: 224px; list-style: none; text-align: right;
    font-size: 12.5px; line-height: 16.5px; color: #fff;
  }
  .contact-list li { display: flex; justify-content: flex-end; align-items: center; gap: 8px; }
  .contact-icon { width: 10px; height: 10px; fill: #d8d0d8; }
</style>
</head>
<body>

<section class="card card-front" aria-label="Card front">
  <div class="front-brand">
    <span class="brand-mark"></span>
    <span class="brand-name">maplebrook</span>
    <span class="brand-sub">pediatric dentistry</span>
  </div>
  <p class="front-url">
    <span class="url-rule"></span>
    <span>www.<span class="url-accent">maplebrookkidsdental</span>.example</span>
    <span class="url-rule"></span>
  </p>
</section>

<section class="card card-back" aria-label="Card back">
  <svg class="back-wave" viewBox="0 0 482 292" width="482" height="292" aria-hidden="true">
    <path d="M0,268 C60,268 250,215 482,148 V292 H0 Z" fill="var(--plum)"/>
    <path d="M0,230 C100,240 200,242 272,232 C190,254 90,262 0,262 Z" fill="var(--magenta)"/>
    <path d="M46,243 C110,246 250,198 482,132 V141 C250,208 110,251 46,243 Z" fill="var(--gold)"/>
  </svg>

  <div class="back-brand">
    <span class="brand-mark"></span>
    <div class="brand-name">maplebrook</div>
    <div class="brand-sub">pediatric dentistry</div>
  </div>

  <h1 class="doctor-name">Corinne Walbeck, DMD</h1>
  <address class="address">
    482 Quarry Lane<br>
    Suite 517 Fernhill, PA 19990
  </address>

  <ul class="contact-list">
    <li>555.555.0193
      <svg class="contact-icon" viewBox="0 0 10 10"><path d="M1,3 C1,1.5 3,1 5,1 C7,1 9,1.5 9,3 L7,3.6 L6.6,2.6 H3.4 L3,3.6 Z M2,5 L3.5,3.8 H6.5 L8,5 V8.5 H2 Z"/></svg>
    </li>
    <li>maplebrookkidsdental.example
      <svg class="contact-icon" viewBox="0 0 10 10"><path d="M0.5,2 H9.5 V8 H0.5 Z M1,2.4 L5,5.4 L9,2.4" stroke="var(--plum)" stroke-width="0.7"/></svg>
    </li>
    <li>name@maplebrookkidsdental.example
      <svg class="contact-icon" viewBox="0 0 10 10"><circle cx="5" cy="5" r="4.3"/><path d="M0.7,5 H9.3 M5,0.7 C3,3 3,7 5,9.3 M5,0.7 C7,3 7,7 5,9.3" stroke="var(--plum)" stroke-width="0.6" fill="none"/></svg>
    </li>
  </ul>
</section>

</body>
</html>
```